Quillmere Air Business Card Design

Design new, 2 sides, business cards for a residential and light commercial heating, air conditioning contractor.

Target Market(s)

Homeowners, small businesses

Industry/Entity Type

Business

Contact Information for Business Card

Dominic Westerhall
Phone - 862-415-2736
Email
Address - PO box 518
Brightwater NJ 07912
Website - www.HarborBreezeLLC.example

Requirements
Must have
• logo, company colors, standard size with no die cut, so I can use nova stamp

```html
<!DOCTYPE html>
<html lang="en">
<head>
<meta charset="utf-8">
<title>Quillmere Air Business Card</title>
<link rel="stylesheet" href="https://fonts.googleapis.com/css2?family=Libre+Baskerville:ital,wght@0,400;0,700;1,400&family=Roboto+Condensed:wght@400;700&display=swap">
<style>
  :root {
    --stage: #e4e1dc;
    --ink: #141414;
    --card-black: #1c1c1c;
    --ghost: #2c2c2c;
    --panel-grey: #8e8e8e;
    --panel-grey-dark: #6f6f6f;
    --paper: #ffffff;
    --paper-shade: #e6e6e6;
    --band: #262626;
    --muted: #555555;
    --light: #f2f2f2;
  }
  * { box-sizing: border-box; margin: 0; padding: 0; }
  html, body { width: 1200px; height: 843px; overflow: hidden; }
  body {
    background: var(--stage);
    display: flex;
    flex-direction: column;
    align-items: center;
    justify-content: center;
    gap: 56px;
  }
  .card {
    position: relative;
    width: 600px;
    height: 343px;
    overflow: hidden;
    box-shadow: 0 6px 18px rgba(0,0,0,.25);
  }

  /* Back side */
  .card-back {
    background: var(--card-black);
    display: flex;
    flex-direction: column;
    align-items: center;
    justify-content: center;
    gap: 14px;
  }
  .ghost-word {
    font-family: "Libre Baskerville", serif;
    font-weight: 700;
    font-size: 46px;
    line-height: 1;
    color: var(--ghost);
    white-space: nowrap;
  }
  .tagline {
    text-align: center;
    font-family: "Libre Baskerville", serif;
    font-size: 17px;
    line-height: 1.35;
    color: var(--light);
  }

  /* Front side */
  .card-front {
    background: linear-gradient(90deg, var(--paper-shade), var(--paper) 45%);
  }
  .brand-panel {
    position: absolute;
    left: 0; top: 0; bottom: 0;
    width: 215px;
    background: var(--panel-grey);
  }
  .brand-strip {
    position: absolute;
    left: 0; top: 82px;
    width: 250px;
    height: 160px;
    background: var(--panel-grey-dark);
    display: flex;
    align-items: center;
    justify-content: center;
    gap: 10px;
  }
  .brand-dot {
    width: 14px; height: 14px;
    border-radius: 50%;
    background: var(--ink);
    flex: none;
  }
  .brand-name {
    font-family: "Libre Baskerville", serif;
    font-weight: 700;
    font-size: 25px;
    line-height: 1.1;
    color: var(--ink);
  }
  .identity {
    position: absolute;
    left: 270px; right: 20px;
    top: 48px;
    text-align: center;
  }
  .person-name {
    font-family: "Libre Baskerville", serif;
    font-size: 27px;
    color: var(--ink);
  }
  .person-role {
    margin-top: 4px;
    font-family: "Libre Baskerville", serif;
    font-style: italic;
    font-size: 14px;
    color: var(--muted);
  }
  .divider {
    display: block;
    margin: 14px auto 14px;
  }
  .contact {
    font-family: "Roboto Condensed", sans-serif;
    font-size: 14px;
    line-height: 1.5;
    color: var(--ink);
    list-style: none;
  }
  .contact b { font-weight: 700; }
  .web-band {
    position: absolute;
    left: 0; right: 0; bottom: 0;
    height: 40px;
    background: var(--band);
    display: flex;
    align-items: center;
    justify-content: flex-end;
    padding-right: 22px;
    font-family: "Roboto Condensed", sans-serif;
    font-size: 15px;
    letter-spacing: 2.5px;
    color: var(--paper);
  }
</style>
</head>
<body>

  <section class="card card-back" aria-label="Card back">
    <div class="ghost-word" aria-hidden="true">Quillmere</div>
    <p class="tagline">Residential &amp; light commercial heating<br>Air conditioning contractor</p>
    <div class="ghost-word" aria-hidden="true">Air</div>
  </section>

  <section class="card card-front" aria-label="Card front">
    <div class="brand-panel"></div>
    <div class="brand-strip">
      <span class="brand-dot"></span>
      <span class="brand-name">Quillmere<br>Air</span>
    </div>

    <div class="identity">
      <h1 class="person-name">Dominic Westerhall</h1>
      <p class="person-role">CEO/Founder</p>
      <svg class="divider" width="120" height="12" viewBox="0 0 120 12" aria-hidden="true">
        <line x1="0" y1="6" x2="120" y2="6" stroke="#9a9a9a" stroke-width="1"/>
        <rect x="56" y="2" width="8" height="8" fill="#141414" transform="rotate(45 60 6)"/>
      </svg>
      <ul class="contact">
        <li>PO box 518</li>
        <li>Brightwater NJ 07912</li>
        <li><b>P.</b> 862 415 2736 <b>M.</b> 862 415 2790</li>
        <li><b>E.</b> dominic@quillmereairllc.example</li>
      </ul>
    </div>

    <div class="web-band">WWW.QUILLMEREAIRLLC.EXAMPLE</div>
  </section>

</body>
</html>
```